Professional Services - letterhead / business cards

The company (velmora partners) will provide services to Investment Funds and large investors in Spain. I have recently chosen a logo that I am attaching.

I would like a simple stationary design that i could use as letter head, business cards and "with compliments" cards.

I am not quite sure which color I will mostly use for the logo, in the email signature I will probably lean towards the white background and grey letters. I am attaching my favourite options.

Target Market(s)

Large Multinationals, Investment funds and Law firms

Industry/Entity Type

Business

Requirements
Must have
• my details are:
Luis R. Abadal
Velmora Partners S.L.
Casa de Torrelumbre
Calle de Vientoalto 27
28014 Madrid
T: +34 (91) 387-2265
M: +34 (646) 819-054
e-mail: labadal@velmorapartners.com

```html
<!DOCTYPE html>
<html lang="en">
<head>
<meta charset="utf-8">
<title>Velmora Partners – Business Cards</title>
<link href="https://fonts.googleapis.com/css2?family=Questrial&family=Source+Sans+3:wght@400;600&display=swap" rel="stylesheet">
<style>
  :root {
    --navy: #1a1f78;
    --ink: #55575c;
    --paper: #ffffff;
    --backdrop: #e9e9ec;
    --rule: #c9c9cc;
  }
  * { box-sizing: border-box; margin: 0; padding: 0; }
  html, body {
    width: 1200px; height: 588px; overflow: hidden;
    background: var(--backdrop);
  }
  .sheet {
    position: relative; width: 1200px; height: 588px;
  }
  .card {
    position: absolute; top: 144px;
    width: 500px; height: 300px;
    background: var(--paper);
    box-shadow: 0 2px 10px rgba(0,0,0,.12);
    overflow: hidden;
  }
  .card--front { left: 70px; }
  .card--back  { left: 630px; }

  /* Front */
  .brand {
    position: absolute; left: 0; right: 0; top: 112px;
    text-align: center;
    font-family: "Questrial", sans-serif;
    font-size: 42px; color: var(--navy);
    letter-spacing: 0.5px;
  }
  .website {
    position: absolute; left: 0; right: 0; top: 186px;
    text-align: center;
    font-family: "Questrial", sans-serif;
    font-size: 13px; color: var(--navy);
    letter-spacing: 4px;
  }

  /* Back */
  .card__edge { position: absolute; }
  .card__edge--left { left: 0; top: 40px; }
  .card__edge--right { right: 0; top: 218px; }

  .brand--small {
    position: absolute; left: 92px; top: 36px;
    font-family: "Questrial", sans-serif;
    font-size: 32px; color: var(--navy);
  }
  .contact {
    position: absolute; left: 70px; top: 112px;
    list-style: none;
    font-family: "Source Sans 3", sans-serif;
    font-size: 13.5px; color: var(--ink); line-height: 19px;
  }
  .contact li { display: flex; align-items: center; gap: 8px; }
  .contact svg { width: 11px; height: 11px; fill: var(--ink); flex: none; }
  .address {
    position: absolute; left: 70px; top: 180px;
    font-family: "Source Sans 3", sans-serif;
    font-style: normal;
    font-size: 13.5px; color: var(--ink); line-height: 19px;
  }
  .holder {
    position: absolute; right: 40px; top: 214px;
    text-align: left;
  }
  .holder__name {
    font-family: "Questrial", sans-serif;
    font-size: 17px; color: var(--navy); letter-spacing: 1px;
    text-transform: uppercase;
  }
  .holder__company {
    font-family: "Source Sans 3", sans-serif;
    font-size: 12px; color: var(--ink);
  }
</style>
</head>
<body>
<main class="sheet">

  <section class="card card--front" aria-label="Business card, front">
    <div class="brand">velmora partners</div>
    <div class="website">www.velmorapartners.com</div>
  </section>

  <section class="card card--back" aria-label="Business card, back">
    <svg class="card__edge card__edge--left" width="16" height="140" viewBox="0 0 16 140" aria-hidden="true">
      <path d="M0 0 H6 Q14 0 14 10 V130 Q14 140 6 140 H0 Z" fill="var(--navy)"/>
    </svg>
    <svg class="card__edge card__edge--right" width="10" height="44" viewBox="0 0 10 44" aria-hidden="true">
      <path d="M10 0 H6 Q0 0 0 8 V36 Q0 44 6 44 H10 Z" fill="var(--navy)"/>
    </svg>

    <div class="brand--small">velmora partners</div>

    <ul class="contact">
      <li>
        <svg viewBox="0 0 12 12" aria-hidden="true"><circle cx="6" cy="6" r="6"/><path d="M4 3 L5 5 L4.4 5.6 Q5.3 7 6.4 7.6 L7 7 L9 8 L8.4 9.2 Q5 9 3 4 Z" fill="#fff"/></svg>
        <span>+34 (91) 387-2265</span>
      </li>
      <li>
        <svg viewBox="0 0 12 12" aria-hidden="true"><rect x="3" y="0" width="6" height="12" rx="1"/><rect x="4" y="1.5" width="4" height="6" fill="#fff"/></svg>
        <span>+34 (646) 819-054</span>
      </li>
      <li>
        <svg viewBox="0 0 12 12" aria-hidden="true"><circle cx="6" cy="6" r="6"/><rect x="3" y="4" width="6" height="4" fill="#fff"/><path d="M3 4 L6 6.5 L9 4" stroke="var(--ink)" stroke-width=".8" fill="none"/></svg>
        <span>labadal@velmorapartners.com</span>
      </li>
    </ul>

    <address class="address">
      Casa de Torrelumbre<br>
      Calle de Vientoalto 27<br>
      28014 Madrid
    </address>

    <div class="holder">
      <div class="holder__name">Luis R. Abadal</div>
      <div class="holder__company">Velmora Partners S.L.</div>
    </div>
  </section>

</main>
</body>
</html>
```